Our companies name is The Gilded Ladle and we specialize in craft cupcakes, what I mean by that is that we bake our cupcakes with craft beer and other alcoholic drinks. We are trying to focus on being elegant but at the same time unpretentious. Since we are incorporating beer in our cupcakes we want the business card to have our logo in the front and our information in the back.

Once we select the best design we will provide the contact information to be added. Thank you.

Industry/Entity Type

Business

Font styles to use
Decorative
Script

Requirements
Must have
• Round corners
Should not have
• Square corners

```html
<!DOCTYPE html>
<html lang="en">
<head>
<meta charset="utf-8">
<title>The Gilded Ladle — Business Card</title>
<link href="https://fonts.googleapis.com/css2?family=Rye&family=Arimo:wght@400;700&display=swap" rel="stylesheet">
<style>
  :root {
    --stage: #e9e6e2;
    --card-black: #050505;
    --card-white: #ffffff;
    --brand-red: #e3202a;
    --ink-white: #f4f4f4;
  }
  * { margin: 0; padding: 0; box-sizing: border-box; }
  html, body {
    width: 1200px; height: 848px; overflow: hidden;
    background: var(--stage);
  }
  .canvas {
    width: 1200px; height: 848px;
    display: flex; flex-direction: column;
    align-items: center; justify-content: center; gap: 40px;
  }
  .card {
    position: relative;
    width: 640px; height: 366px;
    border-radius: 18px;
    overflow: hidden;
    background: var(--card-black);
    box-shadow: 0 6px 18px rgba(0,0,0,.25);
  }
  .card-front .swoosh {
    position: absolute; inset: 0; width: 100%; height: 100%;
  }
  .brand-mark {
    display: flex; align-items: center; gap: 10px;
    font-family: "Arimo", sans-serif;
    font-weight: 700;
    white-space: nowrap;
  }
  .brand-mark .dot {
    width: 14px; height: 14px; border-radius: 50%;
    background: var(--brand-red);
    flex: none;
  }
  .card-front .brand-mark {
    position: absolute;
    top: 40px; right: 42px;
    font-size: 21px; color: var(--card-black);
  }
  .employee {
    position: absolute; left: 40px; top: 168px;
  }
  .employee-name {
    font-family: "Rye", serif;
    font-size: 30px; color: var(--brand-red);
    letter-spacing: 1px; line-height: 1;
  }
  .employee-role {
    font-family: "Arimo", sans-serif;
    font-size: 15px; color: var(--ink-white);
    margin-top: 4px;
  }
  .contact-list {
    position: absolute; left: 40px; top: 240px;
    list-style: none;
    font-family: "Arimo", sans-serif;
    font-size: 15px; color: var(--ink-white);
  }
  .contact-list li {
    display: flex; align-items: center; gap: 10px;
    height: 22px;
  }
  .contact-list svg { width: 14px; height: 14px; fill: var(--brand-red); flex: none; }
  .contact-list .address { margin-top: 4px; font-size: 16px; }

  .card-back .divider {
    position: absolute; left: 0; right: 0; top: 182px;
    height: 2px; background: var(--brand-red);
  }
  .card-back .brand-seal {
    position: absolute; left: 50%; top: 50%;
    transform: translate(-50%, -50%);
    padding: 14px 26px;
    background: var(--card-black);
  }
  .card-back .brand-mark {
    font-size: 28px; color: var(--ink-white);
  }
</style>
</head>
<body>
<main class="canvas">

  <section class="card card-front" aria-label="Business card, contact side">
    <svg class="swoosh" viewBox="0 0 640 366" preserveAspectRatio="none" aria-hidden="true">
      <path d="M150 0 C 300 80 470 150 640 128 L640 0 Z" fill="var(--card-white)"/>
      <path d="M112 0 C 270 98 460 170 640 146 L640 128 C 470 150 300 80 150 0 Z" fill="var(--brand-red)"/>
    </svg>

    <div class="brand-mark"><span class="dot"></span>The Gilded Ladle</div>

    <div class="employee">
      <div class="employee-name">EMPLOYEE NAME</div>
      <div class="employee-role">Managing Director</div>
    </div>

    <ul class="contact-list">
      <li>
        <svg viewBox="0 0 16 16" aria-hidden="true"><path d="M3 2l3 0 1 4-2 1c1 2 2 3 4 4l1-2 4 1v3c-6 0-11-5-11-11z"/></svg>
        (xxx) xxx-xxxx
      </li>
      <li>
        <svg viewBox="0 0 16 16" aria-hidden="true"><path d="M4 1h8v4H4zM1 6h14v6h-3v3H4v-3H1zM5 10v4h6v-4z"/></svg>
        xxx xxx xxxx
      </li>
      <li>
        <svg viewBox="0 0 16 16" aria-hidden="true"><circle cx="8" cy="8" r="7"/><path d="M1 8h14M8 1c3 3 3 11 0 14M8 1c-3 3-3 11 0 14" stroke="#050505" stroke-width="1.2" fill="none"/></svg>
        www.yourwebsit.com
      </li>
      <li>
        <svg viewBox="0 0 16 16" aria-hidden="true"><path d="M1 3h14v10H1z"/><path d="M1 3l7 6 7-6" stroke="#050505" stroke-width="1.3" fill="none"/></svg>
        Info@youremail.com
      </li>
      <li class="address">Your Address Inc 2nd Lane Ave Brookfield,NJ&nbsp;&nbsp;00000</li>
    </ul>
  </section>

  <section class="card card-back" aria-label="Business card, logo side">
    <div class="divider"></div>
    <div class="brand-seal">
      <div class="brand-mark"><span class="dot"></span>The Gilded Ladle</div>
    </div>
  </section>

</main>
</body>
</html>
```